Looking for a modern, Professional business card design

We have a simple business card, but are looking for a more modern, professional look. A sample of the basic card is attached as well as the logo. We would also like to add that we offer:
Struggling with your finances?
- Learn to become debt free
- Discover the power of cash
- Control your money instead of it controlling you
Let us help you achieve a new level of financial freedom!
Also, we would like to have a "SPECIAL OFFER!: FREE 30 minute consultation"
Financial Planning

```html
<!DOCTYPE html>
<html lang="en">
<head>
<meta charset="utf-8">
<title>Summit Money Coaching — Business Card</title>
<link href="https://fonts.googleapis.com/css2?family=Open+Sans:ital,wght@0,400;0,600;0,700;1,400&display=swap" rel="stylesheet">
<style>
  :root {
    --stage: #3b3b3b;
    --paper: #ffffff;
    --green: #4c9a2a;
    --green-dark: #3c8f3a;
    --green-bright: #a6d03a;
    --ink: #222222;
    --ink-soft: #555555;
    --rule: #bdbdbd;
  }
  * { box-sizing: border-box; margin: 0; padding: 0; }
  html, body { width: 1105px; height: 1200px; overflow: hidden; }
  body {
    background: var(--stage);
    font-family: "Open Sans", Arial, sans-serif;
    position: relative;
  }
  .card {
    position: absolute;
    left: 193px;
    width: 720px;
    height: 412px;
    overflow: hidden;
  }
  /* Front */
  .card-front { top: 181px; background: var(--paper); }
  .accent-tab {
    position: absolute; left: 0; top: 95px; width: 15px; height: 50px;
    background: linear-gradient(90deg, var(--green-bright), var(--green));
  }
  .holder-name {
    position: absolute; left: 41px; top: 88px;
    font-size: 27px; line-height: 34px; font-weight: 600; color: var(--green); letter-spacing: 0.3px;
  }
  .holder-title {
    position: absolute; left: 41px; top: 123px;
    font-size: 20px; line-height: 28px; color: var(--ink);
  }
  .header-rule {
    position: absolute; left: 41px; top: 159px; width: 636px; height: 1px;
    background: var(--rule);
  }
  .brand-front {
    position: absolute; right: 45px; top: 72px;
    display: flex; align-items: center; gap: 14px;
  }
  .brand-dot {
    width: 34px; height: 34px; border-radius: 50%; background: var(--green); flex: none;
  }
  .brand-name {
    font-size: 26px; line-height: 31px; font-weight: 700; color: var(--ink);
    letter-spacing: 0.5px; text-align: left;
  }
  .contact {
    position: absolute; left: 0; width: 100%;
    display: flex; justify-content: center; gap: 18px;
    font-size: 19px; line-height: 26px; color: var(--ink-soft);
  }
  .contact-row-1 { top: 318px; }
  .contact-row-2 { top: 346px; }
  .contact-item { display: flex; align-items: center; gap: 8px; }
  .contact-item svg { fill: var(--green); flex: none; }

  /* Back */
  .card-back {
    top: 637px;
    background: radial-gradient(ellipse 60% 75% at 48% 55%, var(--green-bright) 0%, #7dbb3a 40%, var(--green-dark) 100%);
    color: #fff;
    text-align: right;
  }
  .pitch { position: absolute; right: 22px; top: 52px; }
  .pitch-heading { font-size: 19px; font-weight: 700; letter-spacing: 0.2px; margin-bottom: 4px; margin-right: 22px; }
  .pitch-list { list-style: none; font-size: 19px; font-style: italic; line-height: 25px; }
  .pitch-list li::after {
    content: ""; display: inline-block; width: 9px; height: 9px; border-radius: 50%;
    background: #fff; margin-left: 12px; vertical-align: middle;
  }
  .pitch-close { font-size: 19px; font-style: italic; line-height: 25px; }
  .offer { position: absolute; right: 43px; top: 198px; }
  .offer-title { font-size: 25px; font-weight: 700; line-height: 32px; }
  .offer-detail { font-size: 17px; font-weight: 700; }
  .brand-back { position: absolute; right: 39px; top: 264px; font-weight: 700; }
  .brand-back-main { font-size: 62px; line-height: 70px; letter-spacing: 1px; }
  .brand-back-sub { font-size: 21px; letter-spacing: 0.5px; }
</style>
</head>
<body>
  <section class="card card-front" aria-label="Business card front">
    <div class="accent-tab"></div>
    <h1 class="holder-name">DANIEL R. HAYES</h1>
    <p class="holder-title">Personal Financial Coach</p>
    <div class="brand-front">
      <span class="brand-dot"></span>
      <span class="brand-name">SUMMIT<br>MONEY COACHING</span>
    </div>
    <div class="header-rule"></div>
    <div class="contact contact-row-1">
      <span class="contact-item">
        <svg width="12" height="20" viewBox="0 0 12 20"><rect x="0" y="0" width="12" height="20" rx="2"/><rect x="2" y="3" width="8" height="12" fill="#fff"/></svg>
        (205) 555-0187
      </span>
      <span class="contact-item">
        <svg width="18" height="13" viewBox="0 0 18 13"><rect width="18" height="13" rx="1"/><path d="M1 1 L9 7 L17 1" stroke="#fff" stroke-width="1.5" fill="none"/></svg>
        daniel@steadyledgercoaching.com
      </span>
    </div>
    <div class="contact contact-row-2">
      <span class="contact-item">
        <svg width="17" height="17" viewBox="0 0 17 17"><circle cx="8.5" cy="8.5" r="8.5"/><path d="M3 6 Q6 4 8 7 Q9 10 6 11 Z M10 3 Q13 5 12 9 Q14 12 11 14 Q10 11 9 10 Z" fill="#fff"/></svg>
        www.steadyledgercoaching.com
      </span>
    </div>
  </section>

  <section class="card card-back" aria-label="Business card back">
    <div class="pitch">
      <h2 class="pitch-heading">STRUGGLING WITH YOUR FINANCES?</h2>
      <ul class="pitch-list">
        <li>Learn to become debt free</li>
        <li>Discover the power of cash</li>
        <li>Control your money instead of it controlling you</li>
      </ul>
      <p class="pitch-close">Let us help you achieve a new level of financial freedom!</p>
    </div>
    <div class="offer">
      <p class="offer-title">SPECIAL OFFER!</p>
      <p class="offer-detail">FREE 30 minute consultation</p>
    </div>
    <div class="brand-back">
      <p class="brand-back-main">SUMMIT</p>
      <p class="brand-back-sub">MONEY COACHING</p>
    </div>
  </section>
</body>
</html>
```